Mandala Postcard Design

I am in need of a postcard to hand out at a Psychic Fair. I envision the card to having half-of-a Mandala (from my Facebook folder), touched up a bit to make it vibrant and bold. Others vendors will have cards w/photographic backgrounds doing yoga. I'd like mine to stand out for it's line-drawn "cartoonish" nature, solid-color nature. The wording would be my basic contact info and a short description ... something like: "Experience the Magic of Mandala Making ... Next Class will be held: (open space for writing, no lines) The art is contained in this Facebook folder. Lots to choose from, with my favorites being the stronger outlined designs.

https://www.examplesocial.net/Brightorbs/media_set?set=a.20462926615637197.2184852941.783542196&type=3
Updates

I just uploaded a few new drawings that might work better, since they are more round. I want to minimize the white space, for instance, avoid having the left & right corners empty. Another idea could be to use 1/4 mandalas in the corners. I'm ready to make a decision. I want it to look great, but as I gain drawing experience, I'll need to update my cards. Thanks! I'm not sure if this the place for this comment, but I'll also be needing a DVD label for my tutorials, and a front page design for a mandala coloring book.

Target Market(s)

Primarily women interested in metaphysical, psychic, meditation, reiki and a basic interest in art.

Font styles to use
Serif
Sans Serif

Requirements
Should not have
• Should not be on a dark card, really should be a plain white background, it seems, in order to stand out.

```html
<!DOCTYPE html>
<html lang="en">
<head>
<meta charset="utf-8">
<title>Mandala Making Postcard</title>
<link rel="stylesheet" href="https://fonts.googleapis.com/css2?family=Sacramento&family=Arimo:wght@400&display=swap">
<style>
  :root {
    --card-white: #f7f7f8;
    --ink: #2b2b2e;
    --teal: #5cc3cc;
    --sky: #4aa6e0;
    --sun: #f5eb8c;
    --rose: #f094b5;
    --coral: #ee6b6b;
    --lilac: #b993d6;
  }
  * { box-sizing: border-box; margin: 0; padding: 0; }
  html, body {
    width: 1200px;
    height: 800px;
    overflow: hidden;
    background: var(--card-white);
  }
  .postcard {
    position: relative;
    width: 1200px;
    height: 800px;
    background: var(--card-white);
  }
  .art {
    position: absolute;
    display: block;
  }
  .mandala-main { left: 10px; top: 160px; width: 540px; height: 466px; }
  .corner-top-left { left: 0; top: 0; width: 206px; height: 210px; }
  .corner-bottom-left { left: 0; top: 564px; width: 218px; height: 236px; }
  .corner-top-right { left: 906px; top: 0; width: 294px; height: 228px; }
  .corner-bottom-right { left: 731px; top: 470px; width: 469px; height: 330px; }

  .headline {
    position: absolute;
    left: 560px;
    top: 240px;
    width: 520px;
    text-align: center;
    font-family: "Sacramento", cursive;
    font-weight: 400;
    font-size: 62px;
    line-height: 72px;
    color: var(--ink);
  }
  .next-class {
    position: absolute;
    left: 605px;
    top: 408px;
    font-family: "Arimo", sans-serif;
    font-size: 17px;
    color: var(--ink);
  }
</style>
</head>
<body>
<main class="postcard">
  <svg class="art mandala-main" viewBox="0 0 540 466" role="img" aria-label="Hand-drawn colourful mandala with teal petal rim, pink ring and yellow and blue centre">
    <defs>
      <radialGradient id="mandalaTones" cx="50%" cy="50%" r="50%">
        <stop offset="0%" stop-color="#f094b5"/>
        <stop offset="35%" stop-color="#f5eb8c"/>
        <stop offset="62%" stop-color="#4aa6e0"/>
        <stop offset="78%" stop-color="#f094b5"/>
        <stop offset="100%" stop-color="#5cc3cc"/>
      </radialGradient>
    </defs>
    <ellipse cx="270" cy="233" rx="268" ry="231" fill="url(#mandalaTones)"/>
  </svg>

  <svg class="art corner-top-left" viewBox="0 0 206 210" role="img" aria-label="Quarter mandala ornament in yellow, pink and teal">
    <defs>
      <radialGradient id="cornerTL" cx="0%" cy="0%" r="100%">
        <stop offset="0%" stop-color="#f5eb8c"/>
        <stop offset="55%" stop-color="#f094b5"/>
        <stop offset="100%" stop-color="#5cc3cc" stop-opacity="0"/>
      </radialGradient>
    </defs>
    <rect width="206" height="210" fill="url(#cornerTL)"/>
  </svg>

  <svg class="art corner-bottom-left" viewBox="0 0 218 236" role="img" aria-label="Quarter mandala ornament in lilac, pink and yellow">
    <defs>
      <radialGradient id="cornerBL" cx="0%" cy="100%" r="100%">
        <stop offset="0%" stop-color="#b993d6"/>
        <stop offset="50%" stop-color="#f094b5"/>
        <stop offset="100%" stop-color="#f5eb8c" stop-opacity="0"/>
      </radialGradient>
    </defs>
    <rect width="218" height="236" fill="url(#cornerBL)"/>
  </svg>

  <svg class="art corner-top-right" viewBox="0 0 294 228" role="img" aria-label="Quarter mandala ornament with red, pink and blue tile pattern">
    <defs>
      <radialGradient id="cornerTR" cx="100%" cy="0%" r="100%">
        <stop offset="0%" stop-color="#ee6b6b"/>
        <stop offset="50%" stop-color="#f094b5"/>
        <stop offset="100%" stop-color="#4aa6e0" stop-opacity="0"/>
      </radialGradient>
    </defs>
    <rect width="294" height="228" fill="url(#cornerTR)"/>
  </svg>

  <svg class="art corner-bottom-right" viewBox="0 0 469 330" role="img" aria-label="Quarter mandala ornament with blue, pink and yellow petals">
    <defs>
      <radialGradient id="cornerBR" cx="100%" cy="100%" r="100%">
        <stop offset="0%" stop-color="#f5eb8c"/>
        <stop offset="40%" stop-color="#f094b5"/>
        <stop offset="75%" stop-color="#4aa6e0"/>
        <stop offset="100%" stop-color="#5cc3cc" stop-opacity="0"/>
      </radialGradient>
    </defs>
    <rect width="469" height="330" fill="url(#cornerBR)"/>
  </svg>

  <h1 class="headline">Experience the Magic of<br>Mandala Making</h1>
  <p class="next-class">Next Class will be held :</p>
</main>
</body>
</html>
```